Tovel & Associates - London New Letting and Property Management Company *

Tovel & Associates LTD is a new company based in London, and works with brand new residential property in the city centre.

We are aiming to have 1000 new properties a year.

We are looking for something modern and minimalistic :
Logo ,Monogram, Paper Head and Business Card.

Target Market(s)

Internation landlords

Industry/Entity Type

Real Estate

Logo Text

Tovel & Associates

Colors

Designer to choose colors to be used in the design.

Requirements
Nice to have
• A particular monogram with "TA"
Should not have
• Little House over the logo

```html
<!DOCTYPE html>
<html lang="en">
<head>
<meta charset="utf-8">
<title>Tovel &amp; Associates – Business Card</title>
<link href="https://fonts.googleapis.com/css2?family=Work+Sans:wght@400;500;600&display=swap" rel="stylesheet">
<style>
  :root {
    --navy: #184a6e;
    --navy-deep: #123a58;
    --bright: #2a8fc8;
    --ink: #5a5f66;
    --paper: #f4f4f4;
    --paper-shade: #e6e6e6;
    --backdrop: #2e3033;
    --pale: #d9dde0;
  }
  * { margin: 0; padding: 0; box-sizing: border-box; }
  html, body { width: 1200px; height: 900px; overflow: hidden; }
  body {
    background: var(--backdrop);
    font-family: "Work Sans", Arial, sans-serif;
    display: flex;
    flex-direction: column;
    align-items: center;
    justify-content: center;
    gap: 50px;
  }
  .card {
    width: 700px;
    height: 400px;
    position: relative;
    box-shadow: 0 18px 40px rgba(0,0,0,.45);
  }
  .card-front {
    background: linear-gradient(135deg, var(--paper-shade) 0%, #fafafa 45%, var(--paper) 100%);
    display: flex;
    align-items: center;
  }
  .brand {
    width: 340px;
    display: flex;
    align-items: center;
    justify-content: center;
    gap: 14px;
  }
  .brand-square {
    width: 34px; height: 34px;
    background: var(--navy);
    flex: none;
  }
  .brand-name {
    font-weight: 600;
    font-size: 22px;
    letter-spacing: 1.5px;
    text-transform: uppercase;
    color: var(--navy);
    line-height: 1.25;
  }
  .divider {
    width: 2px;
    height: 180px;
    background: var(--navy);
  }
  .details {
    padding-left: 46px;
    color: var(--ink);
    font-size: 17px;
    line-height: 1.45;
  }
  .person-name {
    font-size: 30px;
    font-weight: 500;
    letter-spacing: 2px;
    color: var(--navy);
    text-transform: uppercase;
    line-height: 1.1;
  }
  .person-role { margin-bottom: 8px; }
  .address { margin-bottom: 6px; }
  .contact-row { display: flex; align-items: center; gap: 9px; }
  .contact-row svg { width: 13px; height: 13px; flex: none; }
  .web-domain { color: var(--navy); font-weight: 600; }

  .card-back {
    background: linear-gradient(160deg, var(--navy) 0%, var(--navy-deep) 100%);
    display: flex;
    align-items: center;
    justify-content: center;
    gap: 18px;
  }
  .card-back .brand-square { background: var(--pale); width: 44px; height: 44px; }
  .card-back .brand-name { color: var(--pale); font-size: 30px; }
</style>
</head>
<body>
  <section class="card card-front" aria-label="Business card front">
    <div class="brand">
      <span class="brand-square"></span>
      <span class="brand-name">Tovel &amp;<br>Associates</span>
    </div>
    <div class="divider"></div>
    <div class="details">
      <div class="person-name">Daniel Hartwell</div>
      <div class="person-role">Director</div>
      <div class="address">14 Caldon Row<br>London EC2A 4PN</div>
      <div class="contact-row">
        <svg viewBox="0 0 16 16" aria-hidden="true"><path fill="#184a6e" d="M4 1l2.5 3-1.5 2c1 2 3 4 5 5l2-1.5 3 2.5-2 2.5C7 14 2 9 1.5 3.5z"/></svg>
        +44 20 7946 0321
      </div>
      <div class="contact-row">
        <svg viewBox="0 0 16 16" aria-hidden="true"><rect x="1" y="3" width="14" height="10" fill="none" stroke="#184a6e" stroke-width="1.6"/><path d="M1 3l7 6 7-6" fill="none" stroke="#184a6e" stroke-width="1.6"/></svg>
        hello@tovelassociates.com
      </div>
      <div class="contact-row">
        <svg viewBox="0 0 16 16" aria-hidden="true"><circle cx="8" cy="8" r="6.5" fill="none" stroke="#184a6e" stroke-width="1.5"/><ellipse cx="8" cy="8" rx="3" ry="6.5" fill="none" stroke="#184a6e" stroke-width="1.2"/><path d="M1.5 8h13" stroke="#184a6e" stroke-width="1.2"/></svg>
        <span>www.<span class="web-domain">tovelassociates</span>.com</span>
      </div>
    </div>
  </section>

  <section class="card card-back" aria-label="Business card back">
    <span class="brand-square"></span>
    <span class="brand-name">Tovel &amp; Associates</span>
  </section>
</body>
</html>
```